Hvac and insulation company needs good looking business card design

We are hvac and insulation company and looking for a new business cards that look to today standards designs

Target Market(s)

homeowners

Industry/Entity Type

Hvac

Contact Information for Business Card

Name: Walter Brinoku
Home comfort consultant
address: 4827 Dunmore St #215 Oakland, CA 94619
office: 888-316-2790
cell: 510-742-3185
Lic.# 584261
Email: walter@corvane-hvac.com
Web: corvane-hvac.com

Requirements
Must have
• clean and sleek look
Nice to have
• simple with a clean look
Should not have
• to busy business card

```html
<!DOCTYPE html>
<html lang="en">
<head>
<meta charset="utf-8">
<title>Corvane Home Solutions – Business Card</title>
<link href="https://fonts.googleapis.com/css2?family=Arimo:wght@400;700&display=swap" rel="stylesheet">
<style>
  :root {
    --orange: #f5821f;
    --ink: #3a3a3a;
    --grey: #8a8a8a;
    --rule: #c9c9c9;
    --paper: #ffffff;
    --card-back: #141414;
    --backdrop: #e9e7e4;
  }
  * { box-sizing: border-box; margin: 0; padding: 0; }
  html, body { width: 1200px; height: 844px; overflow: hidden; }
  body {
    background: var(--backdrop);
    font-family: "Arimo", Arial, sans-serif;
    position: relative;
  }
  .card {
    position: absolute;
    top: 272px;
    width: 525px;
    height: 300px;
    border-radius: 4px;
    box-shadow: 0 6px 18px rgba(0,0,0,.18);
  }
  .card-front { left: 50px; background: var(--paper); color: var(--ink); }
  .card-back { left: 625px; background: var(--card-back); }

  .license {
    position: absolute; left: 24px; top: 52px;
    font-size: 14px; color: var(--ink);
  }
  .license .label { color: var(--orange); }

  .brand {
    position: absolute; left: 168px; top: 26px;
    display: flex; align-items: center; gap: 14px;
  }
  .brand-square { width: 54px; height: 54px; background: var(--orange); flex: none; }
  .brand-name {
    font-size: 58px; font-weight: 700; color: var(--orange);
    line-height: 1; letter-spacing: -1px;
  }
  .brand-tagline {
    position: absolute; left: 238px; top: 92px;
    font-size: 17px; color: var(--grey); letter-spacing: 2px;
  }

  .rule { position: absolute; height: 1px; background: var(--rule); }
  .rule-top { left: 200px; right: 24px; top: 128px; }
  .rule-mid { left: 24px; right: 24px; top: 158px; }
  .rule-bottom { left: 24px; right: 24px; top: 256px; }

  .person { position: absolute; left: 24px; top: 168px; }
  .person-name { font-size: 22px; font-weight: 700; color: var(--orange); line-height: 1.1; }
  .person-title { font-size: 14px; color: var(--ink); margin-top: 1px; }

  .contact { position: absolute; left: 24px; top: 214px; font-size: 14px; line-height: 20px; }
  .contact .key { color: var(--orange); font-weight: 700; }
  .contact .web { color: var(--orange); }
  .contact .sep { color: var(--grey); }

  .address { position: absolute; left: 24px; top: 266px; font-size: 14px; }

  .back-brand {
    position: absolute; right: 70px; top: 126px;
    display: flex; align-items: center; gap: 8px;
  }
  .back-brand .brand-square { width: 20px; height: 20px; }
  .back-brand .brand-name { font-size: 28px; letter-spacing: 0; }
</style>
</head>
<body>
  <section class="card card-front">
    <p class="license"><span class="label">LIC.</span># 584261</p>

    <div class="brand">
      <span class="brand-square"></span>
      <span class="brand-name">corvane</span>
    </div>
    <p class="brand-tagline">home solutions</p>

    <div class="rule rule-top"></div>
    <div class="rule rule-mid"></div>

    <div class="person">
      <h1 class="person-name">Walter Brinoku</h1>
      <p class="person-title">Home Comfort Consultant</p>
    </div>

    <div class="contact">
      <p><span class="key">P:</span> 888-316-2790 <span class="sep">|</span> <span class="key">M:</span> 510-742-3185</p>
      <p><span class="key">E:</span> walter@corvane-hvac.com <span class="sep">|</span> <span class="web">www.corvane-hvac.com</span></p>
    </div>

    <div class="rule rule-bottom"></div>
    <p class="address">4827 Dunmore St #215 Oakland, CA 94619</p>
  </section>

  <section class="card card-back" role="img" aria-label="Black card back with a faint repeating brand pattern">
    <div class="back-brand">
      <span class="brand-square"></span>
      <span class="brand-name">corvane</span>
    </div>
  </section>
</body>
</html>
```